Vantro cards

I am in the auto motive, transportation business I would like a business card that is Something cool, modern edgy, having to do with car culture. I offer towing service for high and exotic cars. I also provide towing for collisions and car accidents. I offer open and enclosed transport nationwide.

Target Market(s)

Car culture people high end auto collectors

Industry/Entity Type

Towing car carrier

Contact Information for Business Card

My company colors black yellow and silver

Font styles to use
Serif

```html
<!DOCTYPE html>
<html lang="en">
<head>
<meta charset="utf-8">
<title>Vantro cards</title>
<link rel="stylesheet" href="https://fonts.googleapis.com/css2?family=Rokkitt:wght@400;700&family=Lato:wght@400&display=swap">
<style>
  :root {
    --backdrop: #2a2a2a;
    --card-white: #ffffff;
    --brand-yellow: #fbdf5c;
    --panel-black: #1f1f1f;
    --card-black: #222222;
    --silver: #cfcfcf;
    --ink: #111111;
    --text-light: #f2f2f2;
  }
  * { margin: 0; padding: 0; box-sizing: border-box; }
  html, body {
    width: 1200px; height: 1122px; overflow: hidden;
    background: var(--backdrop);
  }
  .canvas {
    position: relative; width: 1200px; height: 1122px;
  }
  .card {
    position: absolute; left: 160px; width: 880px; height: 503px;
    border-radius: 32px; overflow: hidden;
  }
  .card-front { top: 38px; background: var(--card-white); }
  .card-back { top: 581px; background: var(--card-black); }

  .yellow-band {
    position: absolute; left: 0; top: 70px; width: 360px; height: 262px;
    background: var(--brand-yellow);
  }
  .info-panel {
    position: absolute; left: 350px; top: 170px; right: 0; height: 262px;
    background: var(--panel-black);
    padding: 34px 0 0 78px;
  }
  .brand-mark {
    position: absolute; display: flex; align-items: center; gap: 12px;
    font-family: "Rokkitt", serif; font-weight: 700;
    white-space: nowrap; line-height: 1;
  }
  .card-front .brand-mark {
    left: 36px; top: 150px; font-size: 76px; color: var(--ink);
    z-index: 1;
  }
  .card-front .brand-dot {
    width: 22px; height: 22px; border-radius: 50%; background: var(--ink);
  }
  .card-back .brand-mark {
    left: 0; right: 0; top: 0; bottom: 0; justify-content: center;
    font-size: 120px; color: var(--silver);
  }
  .card-back .brand-dot {
    width: 32px; height: 32px; border-radius: 50%; background: var(--silver);
  }
  .person-name {
    font-family: "Rokkitt", serif; font-weight: 400;
    font-size: 40px; letter-spacing: 2px; color: var(--brand-yellow);
    line-height: 1;
  }
  .person-title {
    font-family: "Lato", sans-serif; font-size: 22px;
    color: var(--text-light); margin-top: 6px;
  }
  .contact-list {
    list-style: none; margin-top: 26px;
  }
  .contact-list li {
    display: flex; align-items: center; gap: 14px;
    font-family: "Lato", sans-serif; font-size: 21px;
    color: var(--text-light); line-height: 1.55;
  }
  .contact-icon { width: 16px; height: 16px; flex: none; }
</style>
</head>
<body>
<main class="canvas">
  <section class="card card-front" aria-label="Business card front">
    <div class="yellow-band"></div>
    <div class="brand-mark"><span class="brand-dot"></span>Vantro</div>
    <div class="info-panel">
      <p class="person-name">MARCUS HALE</p>
      <p class="person-title">Managing Director</p>
      <ul class="contact-list">
        <li>
          <svg class="contact-icon" viewBox="0 0 16 16" aria-hidden="true"><path fill="var(--brand-yellow)" d="M3 1l3 3-1.6 1.8a9 9 0 0 0 6 6L12.2 10l3 3-2 2C7 15 1 9 1 3z"/></svg>
          555-014-2290
        </li>
        <li>
          <svg class="contact-icon" viewBox="0 0 16 16" aria-hidden="true"><rect x="1" y="3" width="14" height="10" fill="var(--brand-yellow)"/><path d="M1 3l7 6 7-6" fill="none" stroke="var(--panel-black)" stroke-width="1.4"/></svg>
          info@vantrotow.com
        </li>
        <li>
          <svg class="contact-icon" viewBox="0 0 16 16" aria-hidden="true"><circle cx="8" cy="8" r="7" fill="var(--brand-yellow)"/><path d="M1 8h14M8 1c-3 3-3 11 0 14M8 1c3 3 3 11 0 14" fill="none" stroke="var(--panel-black)" stroke-width="1.1"/></svg>
          vantrotow.com
        </li>
      </ul>
    </div>
  </section>

  <section class="card card-back" aria-label="Business card back">
    <div class="brand-mark"><span class="brand-dot"></span>Vantro</div>
  </section>
</main>
</body>
</html>
```